Business Cards for IT Consulting Company (Managed Service Provider)

I am looking to have some business cards printed and would like some designs. We are an IT Consulting company based in Vancouver BC. I would like a nice clean and modern look to the cards. I have uploaded all the versions of my logo so parts can be used as needed. Here is a snippit from our website homepage:

Quillbrook Networks Ltd. is an IT Solutions Partner located in Vancouver BC, Canada. We offer IT solutions and support to customers in the greater Vancouver Area. With expertise in Microsoft platforms, as well as Linux and Mac OSX and over 12 years experience in the IT industry, Quillbrook Networks is dedicated to offering our clients top quality service and products. We take pride in the solutions we offer our customers. The greatest compliment a client can give us is to recommend our services.

Quillbrook Networks Ltd. offers a wide range of IT services from onsite service to remote support and managed service solutions. This allows clients to choose the support path that best suits their company’s needs. Supporting many different sized companies from small to enterprise level over the past 12 years Quillbrook Networks has the experience and expertise needed to ensure things run smoothly. Allowing our clients to focus on doing business.

Revolutionizing the way IT services are delivered.

Quillbrook Networks is dedicated to providing our clients with IT solutions that work and grow with them for years to come. This philosophy helps save money in the long run instead of replacing equipment constantly. Far too often IT solutions are not well thought out and while possibly solving the problem at hand, require replacement due to growth or quality within a very short time frame. Quillbrook Networks takes pride in providing solutions that will last and be able to accommodate growth without the need for replacement.

Industry/Entity Type

Information Technology

Contact Information for Business Card

Quillbrook Networks Ltd.
(Employee Name)
Eml: (Employees Email Address)
Web: quillbrook.me
Ph: 604-555-0148

Font styles to use
Serif
Sans Serif

Requirements
Must have
• The Company logo and company colors.
Nice to have
• - Our tag line: "Dependable IT, Built to Last" or "Revolutionizing the way IT services are delivered."
• - Also I really like the idea of nature and technology together blending which is sort of where my logo came from so integrating that somehow onto the business cards would be great.

```html
<!DOCTYPE html>
<html lang="en">
<head>
<meta charset="utf-8">
<title>Quillbrook Networks Ltd. – Business Cards</title>
<link rel="stylesheet" href="https://fonts.googleapis.com/css2?family=Montserrat:wght@500;600&family=Source+Sans+3:wght@400;600&display=swap">
<style>
  :root {
    --backdrop: #3b3b3b;
    --card-white: #f7f7f7;
    --brand-blue: #00a3e4;
    --back-blue: #0399d8;
    --swoosh-grey: #58595b;
    --text-white: #ffffff;
  }
  * { box-sizing: border-box; margin: 0; padding: 0; }
  html, body {
    width: 1200px; height: 750px; overflow: hidden;
    background: var(--backdrop);
  }
  .canvas { position: relative; width: 1200px; height: 750px; }
  .card {
    position: absolute; top: 228px;
    width: 461px; height: 262px; overflow: hidden;
  }
  .card--front { left: 124px; background: var(--card-white); }
  .card--back { left: 618px; background: var(--back-blue); }

  .front-waves { position: absolute; inset: 0; }

  .brand {
    position: absolute; left: 100px; top: 46px;
    display: flex; align-items: center; gap: 10px;
  }
  .brand__dot {
    width: 28px; height: 28px; border-radius: 50%;
    background: var(--brand-blue);
  }
  .brand__text { display: flex; flex-direction: column; }
  .brand__name {
    font-family: "Montserrat", sans-serif; font-weight: 500;
    font-size: 38px; line-height: 38px; letter-spacing: 0.3px;
    color: var(--brand-blue);
  }
  .brand__sub {
    font-family: "Montserrat", sans-serif; font-weight: 600;
    font-size: 14px; letter-spacing: 1px; color: var(--brand-blue);
    margin-top: 1px;
  }

  .holder {
    position: absolute; right: 243px; top: 175px;
    text-align: right; color: var(--text-white);
    font-family: "Source Sans 3", sans-serif;
  }
  .holder__name { font-size: 20px; font-weight: 600; line-height: 25px; }
  .holder__address { font-size: 12.5px; line-height: 17px; }

  .divider {
    position: absolute; left: 234px; top: 182px;
    width: 1px; height: 56px; background: rgba(255,255,255,0.75);
  }

  .contact-list {
    position: absolute; left: 250px; top: 183px; list-style: none;
    font-family: "Source Sans 3", sans-serif; font-size: 12.5px;
    color: var(--text-white);
  }
  .contact-list li {
    display: flex; align-items: center; gap: 6px; height: 18px;
  }
  .contact-list svg { width: 11px; height: 11px; flex: none; }

  .back-brand {
    position: absolute; left: 22px; top: 182px; color: var(--text-white);
  }
  .back-brand__name {
    font-family: "Montserrat", sans-serif; font-weight: 500;
    font-size: 31px; line-height: 32px; letter-spacing: 0.2px;
  }
  .back-brand__sub {
    font-family: "Montserrat", sans-serif; font-weight: 500;
    font-size: 11.5px; letter-spacing: 0.8px; line-height: 14px;
  }
  .back-brand__tagline {
    font-family: "Source Sans 3", sans-serif; font-weight: 600;
    font-size: 12.5px; line-height: 17px; margin-top: 1px;
  }
</style>
</head>
<body>
<main class="canvas">

  <section class="card card--front" aria-label="Business card front">
    <svg class="front-waves" viewBox="0 0 461 262" width="461" height="262" aria-hidden="true">
      <path d="M3,158 C110,132 290,160 452,120 C300,168 120,140 3,158 Z" fill="var(--swoosh-grey)"/>
      <path d="M0,160 C150,146 300,180 461,124 L461,262 L0,262 Z" fill="var(--brand-blue)"/>
    </svg>

    <div class="brand">
      <span class="brand__dot"></span>
      <div class="brand__text">
        <span class="brand__name">Quillbrook</span>
        <span class="brand__sub">NETWORKS LTD.</span>
      </div>
    </div>

    <div class="holder">
      <p class="holder__name">Daniel Hartley</p>
      <p class="holder__address">4120 Alder Crescent<br>Burnaby, BC V5G 1K3</p>
    </div>

    <span class="divider"></span>

    <ul class="contact-list">
      <li>
        <svg viewBox="0 0 12 12" aria-hidden="true"><path d="M2.5 1 L4.5 1 L5.2 3.6 L4 4.6 C4.7 6 6 7.3 7.4 8 L8.4 6.8 L11 7.5 L11 9.5 C11 10.4 10.3 11 9.5 11 C5 10.6 1.4 7 1 2.5 C1 1.7 1.6 1 2.5 1 Z" fill="#fff"/></svg>
        <span>604-555-0148</span>
      </li>
      <li>
        <svg viewBox="0 0 12 12" aria-hidden="true"><rect x="0.5" y="2.5" width="11" height="7.5" fill="#fff"/><path d="M0.8 2.8 L6 6.8 L11.2 2.8" fill="none" stroke="var(--brand-blue)" stroke-width="1"/></svg>
        <span>dhartley@quillbrook.me</span>
      </li>
      <li>
        <svg viewBox="0 0 12 12" aria-hidden="true"><circle cx="6" cy="6" r="5.3" fill="#fff"/><path d="M1 6 H11 M6 0.8 C3.6 3.5 3.6 8.5 6 11.2 M6 0.8 C8.4 3.5 8.4 8.5 6 11.2" fill="none" stroke="var(--brand-blue)" stroke-width="0.9"/></svg>
        <span>www.quillbrook.me</span>
      </li>
    </ul>
  </section>

  <section class="card card--back" aria-label="Business card back">
    <div class="back-brand">
      <p class="back-brand__name">Quillbrook</p>
      <p class="back-brand__sub">NETWORKS LTD.</p>
      <p class="back-brand__tagline">Dependable IT, Built to Last</p>
    </div>
  </section>

</main>
</body>
</html>
```